Looking for a modern, Professional business card design

We have a simple business card, but are looking for a more modern, professional look. A sample of the basic card is attached as well as the logo. We would also like to add that we offer:
Struggling with your finances?
- Learn to become debt free
- Discover the power of cash
- Control your money instead of it controlling you
Let us help you achieve a new level of financial freedom!
Also, we would like to have a "SPECIAL OFFER!: FREE 30 minute consultation"
Financial Planning

```html
<!DOCTYPE html>
<html lang="en">
<head>
<meta charset="utf-8">
<title>Steady Ledger Coaching – Business Card</title>
<link rel="stylesheet" href="https://fonts.googleapis.com/css2?family=Open+Sans:ital,wght@0,400;0,600;0,700;0,800;1,400&display=swap">
<style>
  :root {
    --bg: #ece9e4;
    --green-deep: #2e8a2c;
    --green-mid: #4fa834;
    --green-light: #9fd14a;
    --green-text: #3c9a2a;
    --ink: #3b3b3b;
    --ink-soft: #555;
    --charcoal: #1f1f1f;
    --white: #ffffff;
    --card-w: 540px;
    --card-h: 309px;
  }
  * { box-sizing: border-box; margin: 0; padding: 0; }
  html, body {
    width: 1200px; height: 843px; overflow: hidden;
    background: var(--bg);
    font-family: "Open Sans", Arial, sans-serif;
  }
  .stage { position: relative; width: 1200px; height: 843px; }
  .card {
    position: absolute;
    width: var(--card-w); height: var(--card-h);
    border-radius: 18px;
    overflow: hidden;
    box-shadow: 0 10px 24px rgba(0,0,0,.22);
  }

  /* Back side */
  .card--back {
    left: 40px; top: 130px;
    background:
      radial-gradient(ellipse at 62% 45%, var(--green-light) 0%, rgba(159,209,74,0) 55%),
      linear-gradient(160deg, var(--green-mid) 0%, var(--green-deep) 100%);
    color: var(--white);
    padding: 40px 34px;
  }
  .offer-heading { font-size: 17px; font-weight: 700; letter-spacing: .2px; }
  .offer-list { list-style: none; margin: 6px 0 4px; }
  .offer-list li {
    font-size: 15px; font-style: italic; line-height: 1.35;
    padding-left: 18px; position: relative;
  }
  .offer-list li::before {
    content: ""; position: absolute; left: 2px; top: 8px;
    width: 7px; height: 7px; border-radius: 50%; background: var(--white);
  }
  .offer-cta { font-size: 15px; font-style: italic; margin-top: 6px; }
  .special-title { font-size: 22px; font-weight: 800; margin-top: 16px; line-height: 1.1; }
  .special-detail { font-size: 14px; font-weight: 600; }
  .back-brand {
    position: absolute; left: 34px; bottom: 28px;
    font-size: 30px; font-weight: 800; letter-spacing: .5px; color: var(--white);
  }

  /* Front side */
  .card--front {
    left: 620px; top: 404px;
    background: linear-gradient(135deg, #ffffff 0%, #f4f4f4 60%, #e6e6e6 100%);
    color: var(--ink);
  }
  .holder { position: absolute; left: 30px; top: 30px; }
  .holder-name { font-size: 22px; font-weight: 600; color: var(--green-text); }
  .holder-title { font-size: 16px; color: var(--ink); }
  .contact { position: absolute; left: 30px; top: 150px; font-size: 15px; line-height: 1.4; color: var(--ink-soft); }
  .contact-label { font-weight: 700; color: var(--ink); }
  .front-brand {
    position: absolute; right: 30px; bottom: 62px;
    display: flex; align-items: center; gap: 10px;
    font-size: 24px; font-weight: 800; color: var(--charcoal);
  }
  .front-brand-dot { width: 22px; height: 22px; border-radius: 50%; background: var(--green-mid); }
  .front-base { position: absolute; left: 0; bottom: 0; width: 100%; height: 26px; }
</style>
</head>
<body>
<main class="stage">

  <section class="card card--back" aria-label="Business card back">
    <h2 class="offer-heading">STRUGGLING WITH YOUR FINANCES?</h2>
    <ul class="offer-list">
      <li>Learn to become debt free</li>
      <li>Discover the power of cash</li>
      <li>Control your money instead of it controlling you</li>
    </ul>
    <p class="offer-cta">Let us help you achieve a new level of financial freedom!</p>
    <p class="special-title">SPECIAL OFFER!</p>
    <p class="special-detail">FREE 30 minute consultation</p>
    <p class="back-brand">Steady Ledger Coaching</p>
  </section>

  <section class="card card--front" aria-label="Business card front">
    <div class="holder">
      <p class="holder-name">Jonah R. Ellison</p>
      <p class="holder-title">Personal Financial Coach</p>
    </div>
    <div class="contact">
      <p><span class="contact-label">Phone:</span> (205) 555-0142</p>
      <p>jonah@steadyledgercoach.com</p>
      <p>www.steadyledgercoach.com</p>
    </div>
    <div class="front-brand">
      <span class="front-brand-dot"></span>
      <span>Steady Ledger Coaching</span>
    </div>
    <svg class="front-base" viewBox="0 0 540 26" preserveAspectRatio="none" aria-hidden="true">
      <defs>
        <linearGradient id="base-green" x1="0" x2="1">
          <stop offset="0" stop-color="#2e8a2c"/>
          <stop offset="1" stop-color="#9fd14a"/>
        </linearGradient>
        <linearGradient id="base-dark" x1="0" y1="0" x2="0" y2="1">
          <stop offset="0" stop-color="#3a3a3a"/>
          <stop offset="1" stop-color="#111"/>
        </linearGradient>
      </defs>
      <rect x="0" y="0" width="540" height="26" fill="url(#base-dark)"/>
      <path d="M0 0 H120 L140 26 H0 Z" fill="url(#base-green)"/>
    </svg>
  </section>

</main>
</body>
</html>
```